Creative and Minimalistic Label Design Needed for Black Box Packaging of a Set of Stainless Steel...

I need a label design done for my product packaging (black box, see photo). The design should have a premium feel to it whilst not using too many colours. The product is a set of stainless steel straws (see photo). I require 3 labels to be done, one for the front, one for the back, one for underneath the lid. The labels will consist primarily of a black background (to blend in with the black box packaging). My straws will have 4 variations in colour (Original Silver, Posh Gold, Elegant Rose Gold, and Fierce Black). The labels can be different OR the same for all 4 variations (except for the text indicating colour, and the barcode at the back. The contents that will need to be on the labels are as follows (everything else I leave to your creative minds )

For the front:

Logo (does not necessarily have to be in it's original colours, can be changed to greyscale or single colour if required)

‘Premium Stainless Steel Drink Set’

‘Original Silver’ or ‘Posh Gold’ or ‘Elegant Rose Gold’ or Fierce Black’

For the back:

Never touch a plastic straw again! Your new Stainless Steel Drink Set contains the perfect straw for any occasion or choice of drink. Use it at home or on the go and be part of our family, together we can make a difference and help restore our home planet to its healthy beginnings. You’re amazing!

Contents
Small drinking straw
Medium drinking straw
Large drinking straw
Natural curved drinking straw
Mixing/spoon straw
Two Cleaning brushes
Carry pouch

Recycle logo (see attachments)

Barcode (4 different barcodes) + ‘Made in China’ [I have included the PDFs of the barcodes, pls don't include the text underneath]

For under the lid:

Outline sketches in a table (I have sketched an example for you to refer to to have a rough idea of what I mean)

The squares read:
1. Ready for anything!
2. Water/tea/coffee
3. Soft drink/juice/mixed drinks
4. Smoothies/thick shakes
5. Boba
6. Slushies/slurpies

1. Clean when finished [this sketch is supposed to show the nylon brush cleaning inside the straw]
2. Back into pouch, ready to go again!
Note: Carry pouch is hand/machine washable

The black box is 25x14.5 cm so the labels for the front and back will be 23x12.5 cm, and the label for under the lid will be 19x9 cm. I have also attached my logo both with and without the slogan for you to use in your design as you seem fit.
Thank you all!

Target Market(s)

Any age able to drink from a straw. Target is towards people who want to be eco-friendly

Colors

Designer to choose colors to be used in the design.

Requirements
Must have
• Black as the primary background colour for all 3 lables
Should not have
• No more than 4 colours used

```html
<!DOCTYPE html>
<html lang="en">
<head>
<meta charset="utf-8">
<title>Premium Drink Set – Front Labels</title>
<link rel="stylesheet" href="https://fonts.googleapis.com/css2?family=Barlow:wght@400;500&family=Barlow+Condensed:wght@400;500&display=swap">
<style>
  :root {
    --page: #ffffff;
    --label-black: #050505;
    --panel-black: #121212;
    --panel-edge: #1d1d1d;
    --text-light: #e6e6e6;
    --text-muted: #bdbdbd;
    --silver-a: #8f8f8f;
    --silver-b: #f4f4f4;
    --gold-a: #b8901f;
    --gold-b: #f6e27a;
    --rose-a: #c9777a;
    --rose-b: #f7c8c0;
    --black-a: #0c0c0c;
    --black-b: #3a3a3a;
  }
  * { box-sizing: border-box; margin: 0; padding: 0; }
  html, body { width: 1200px; height: 770px; overflow: hidden; background: var(--page); }
  .label-row {
    position: relative; width: 1200px; height: 770px;
    display: flex; gap: 40px; padding: 125px 60px 0;
  }
  .front-label {
    position: relative; width: 240px; height: 520px;
    background: var(--label-black);
  }
  .label-panel {
    position: absolute; left: 20px; right: 20px; top: 22px; bottom: 24px;
    background: radial-gradient(ellipse at 50% 40%, #1a1a1a 0%, var(--panel-black) 55%, #0a0a0a 100%);
    border: 1px solid var(--panel-edge);
  }
  .brand {
    position: absolute; top: 78px; left: 0; right: 0;
    display: flex; justify-content: center; align-items: center; gap: 7px;
    font-family: "Barlow", sans-serif; font-weight: 500; font-size: 25px;
    color: var(--text-light); letter-spacing: 0.2px;
  }
  .brand-dot { width: 14px; height: 14px; border-radius: 50%; background: var(--text-light); }
  .premium-box {
    position: absolute; top: 150px; left: 28px; width: 184px; height: 46px;
    border: 1px solid #8a8a8a; border-bottom: none;
  }
  .premium-word {
    position: absolute; top: 10px; left: 0; right: 0; text-align: center;
    font-family: "Barlow", sans-serif; font-size: 14px; letter-spacing: 13px;
    padding-left: 13px; color: var(--text-light);
  }
  .premium-base {
    position: absolute; bottom: -6px; left: -1px; right: -1px;
    display: flex; align-items: center; gap: 6px;
  }
  .premium-base::before, .premium-base::after {
    content: ""; flex: 1; height: 1px; background: #8a8a8a;
  }
  .premium-sub {
    font-family: "Barlow", sans-serif; font-size: 11.5px; letter-spacing: 1.3px;
    color: var(--text-muted);
  }
  .drink-icon { position: absolute; top: 218px; left: 50%; margin-left: -32px; width: 64px; height: 96px; }
  .product-name {
    position: absolute; top: 330px; left: 0; right: 0; text-align: center;
    font-family: "Barlow", sans-serif; font-weight: 500; font-size: 42px;
    line-height: 0.86; color: var(--text-light); letter-spacing: -0.5px;
  }
  .colour-ribbon {
    position: absolute; top: 422px; left: 50%; margin-left: -73px;
    width: 146px; height: 27px;
    display: flex; align-items: center; justify-content: center;
    font-family: "Barlow Condensed", sans-serif; font-weight: 500; font-size: 17px;
    clip-path: polygon(0 0, 100% 0, 93% 50%, 100% 100%, 0 100%, 7% 50%);
  }
  .silver .colour-ribbon { background: linear-gradient(90deg, var(--silver-b), var(--silver-a) 50%, var(--silver-b)); color: #111; }
  .gold .colour-ribbon { background: linear-gradient(90deg, var(--gold-b), var(--gold-a) 50%, var(--gold-b)); color: #111; }
  .rose .colour-ribbon { background: linear-gradient(90deg, var(--rose-b), var(--rose-a) 50%, var(--rose-b)); color: #111; }
  .black .colour-ribbon { background: linear-gradient(90deg, var(--black-b), var(--black-a) 50%, var(--black-b)); color: #f0f0f0; }
  .silver { --icon: #cfcfcf; }
  .gold { --icon: #d9b848; }
  .rose { --icon: #e4a09b; }
  .black { --icon: #4a4a4a; }
  .drink-icon * { stroke: var(--icon); fill: none; stroke-width: 3; stroke-linecap: round; stroke-linejoin: round; }
</style>
</head>
<body>
<main class="label-row">
  <section class="front-label silver">
    <div class="label-panel"></div>
    <div class="brand"><span class="brand-dot"></span>verdaleaf</div>
    <div class="premium-box"><span class="premium-word">PREMIUM</span><div class="premium-base"><span class="premium-sub">stainless steel</span></div></div>
    <svg class="drink-icon" viewBox="0 0 64 96" aria-hidden="true"><path d="M6 4 L18 12 L28 90"/><path d="M10 34 H44 V84 Q44 92 36 92 H18 Q10 92 10 84 Z"/><path d="M10 52 H44"/><circle cx="48" cy="32" r="13"/><path d="M48 32 L40 42"/></svg>
    <h2 class="product-name">DRINK<br>SET</h2>
    <div class="colour-ribbon">Original Silver</div>
  </section>
  <section class="front-label gold">
    <div class="label-panel"></div>
    <div class="brand"><span class="brand-dot"></span>verdaleaf</div>
    <div class="premium-box"><span class="premium-word">PREMIUM</span><div class="premium-base"><span class="premium-sub">stainless steel</span></div></div>
    <svg class="drink-icon" viewBox="0 0 64 96" aria-hidden="true"><path d="M6 4 L18 12 L28 90"/><path d="M10 34 H44 V84 Q44 92 36 92 H18 Q10 92 10 84 Z"/><path d="M10 52 H44"/><circle cx="48" cy="32" r="13"/><path d="M48 32 L40 42"/></svg>
    <h2 class="product-name">DRINK<br>SET</h2>
    <div class="colour-ribbon">Posh Gold</div>
  </section>
  <section class="front-label rose">
    <div class="label-panel"></div>
    <div class="brand"><span class="brand-dot"></span>verdaleaf</div>
    <div class="premium-box"><span class="premium-word">PREMIUM</span><div class="premium-base"><span class="premium-sub">stainless steel</span></div></div>
    <svg class="drink-icon" viewBox="0 0 64 96" aria-hidden="true"><path d="M6 4 L18 12 L28 90"/><path d="M10 34 H44 V84 Q44 92 36 92 H18 Q10 92 10 84 Z"/><path d="M10 52 H44"/><circle cx="48" cy="32" r="13"/><path d="M48 32 L40 42"/></svg>
    <h2 class="product-name">DRINK<br>SET</h2>
    <div class="colour-ribbon">Elegant Rose Gold</div>
  </section>
  <section class="front-label black">
    <div class="label-panel"></div>
    <div class="brand"><span class="brand-dot"></span>verdaleaf</div>
    <div class="premium-box"><span class="premium-word">PREMIUM</span><div class="premium-base"><span class="premium-sub">stainless steel</span></div></div>
    <svg class="drink-icon" viewBox="0 0 64 96" aria-hidden="true"><path d="M6 4 L18 12 L28 90"/><path d="M10 34 H44 V84 Q44 92 36 92 H18 Q10 92 10 84 Z"/><path d="M10 52 H44"/><circle cx="48" cy="32" r="13"/><path d="M48 32 L40 42"/></svg>
    <h2 class="product-name">DRINK<br>SET</h2>
    <div class="colour-ribbon">Fierce Black</div>
  </section>
</main>
</body>
</html>
```